BUSINESS CARD DESIGN

NAME- DALE VORSKIN
PHONE NUMER - 555- 714-9082
EMAIL- OFFICE@TRV-GROUNDMAKRZ.COM
BACK OF CARD- SPEACIALIZES IN LAND CLEARING, FORESTRY MUCLHING AND EXCAVATION

Contact Information for Business Card

NAME- DALE VORSKIN PHONE NUMER - 555- 714-9082 EMAIL- OFFICE@TRV-GROUNDMAKRZ.COM BACK OF CARD- SPEACIALIZES IN LAND CLEARING , MUCLHING AND EXCAVATION

```html
<!DOCTYPE html>
<html lang="en">
<head>
<meta charset="utf-8">
<title>Terravale Groundmakrz – Business Card</title>
<link href="https://fonts.googleapis.com/css2?family=Roboto+Condensed:wght@300;400;700&display=swap" rel="stylesheet">
<style>
  :root {
    --backdrop: #e3e6e7;
    --card-yellow: #f6b31c;
    --mark-yellow: #fbd03a;
    --card-dark: #212226;
    --decor-dark: #2a2b30;
    --accent: #f6b31c;
    --ink-light: #ffffff;
  }
  * { margin: 0; padding: 0; box-sizing: border-box; }
  html, body {
    width: 1200px; height: 960px; overflow: hidden;
    background: var(--backdrop);
    font-family: "Roboto Condensed", Arial, sans-serif;
  }
  .card {
    position: absolute; left: 250px; width: 702px; height: 400px;
    border-radius: 28px; overflow: hidden;
  }
  /* Front */
  .card-front { top: 60px; background: var(--card-yellow); }
  .front-brand {
    position: absolute; left: 0; right: 0; top: 86px;
    display: flex; flex-direction: column; align-items: center; gap: 22px;
  }
  .front-brand .brand-circle {
    width: 150px; height: 150px; border-radius: 50%;
    background: var(--mark-yellow);
  }
  .front-brand .brand-name {
    color: var(--mark-yellow); font-weight: 700; font-size: 30px;
    letter-spacing: 2px; text-align: center; line-height: 1.1;
  }
  .tagline {
    position: absolute; left: 0; right: 0; top: 357px;
    text-align: center; color: var(--ink-light);
    font-size: 16.5px; letter-spacing: 0.5px;
  }
  /* Back */
  .card-back {
    top: 501px; background: var(--card-dark);
    border: 3px solid var(--accent);
  }
  .back-decor {
    position: absolute; left: 296px; top: 36px;
    width: 400px; height: 400px; border-radius: 50%;
    background: var(--decor-dark);
  }
  .back-brand {
    position: absolute; left: 26px; top: 24px; width: 210px;
    display: flex; flex-direction: column; align-items: center; gap: 14px;
  }
  .back-brand .brand-circle {
    width: 118px; height: 118px; border-radius: 50%;
    background: var(--accent);
  }
  .back-brand .brand-name {
    color: var(--accent); font-weight: 700; font-size: 21px;
    letter-spacing: 1.5px; text-align: center; line-height: 1.15;
  }
  .name-bar {
    position: absolute; left: 0; top: 231px; width: 11px; height: 34px;
    background: var(--accent);
  }
  .person-name {
    position: absolute; left: 19px; top: 226px;
    color: var(--accent); font-size: 35px; letter-spacing: 0.5px; line-height: 1.2;
  }
  .person-name .first { font-weight: 700; }
  .person-name .last { font-weight: 300; }
  .contact-list {
    position: absolute; left: 18px; top: 307px; list-style: none;
  }
  .contact-list li {
    display: flex; align-items: center; gap: 12px;
    height: 21.5px; color: var(--ink-light); font-size: 16px; letter-spacing: 0.6px;
  }
  .contact-list svg { width: 16px; height: 16px; flex: none; }
</style>
</head>
<body>

<section class="card card-front">
  <div class="front-brand">
    <div class="brand-circle"></div>
    <div class="brand-name">TERRAVALE GROUNDMAKRZ</div>
  </div>
  <p class="tagline">SPEACIALIZES IN LAND CLEARING , MUCLHING AND EXCAVATION</p>
</section>

<section class="card card-back">
  <div class="back-decor"></div>
  <div class="back-brand">
    <div class="brand-circle"></div>
    <div class="brand-name">TERRAVALE<br>GROUNDMAKRZ</div>
  </div>
  <div class="name-bar"></div>
  <h1 class="person-name"><span class="first">DALE</span> <span class="last">VORSKIN</span></h1>
  <ul class="contact-list">
    <li>
      <svg viewBox="0 0 24 24" fill="var(--accent)"><path d="M6.6 10.8a15.1 15.1 0 0 0 6.6 6.6l2.2-2.2a1 1 0 0 1 1-.25 11.4 11.4 0 0 0 3.6.57 1 1 0 0 1 1 1V20a1 1 0 0 1-1 1A17 17 0 0 1 3 4a1 1 0 0 1 1-1h3.5a1 1 0 0 1 1 1c0 1.25.2 2.45.57 3.6a1 1 0 0 1-.25 1z"/></svg>
      555- 714-9082
    </li>
    <li>
      <svg viewBox="0 0 24 24" fill="none" stroke="var(--accent)" stroke-width="2"><circle cx="12" cy="12" r="9"/><path d="M3 12h18M12 3c3 3 3 15 0 18M12 3c-3 3-3 15 0 18"/></svg>
      WWW.TRV-GROUNDMAKRZ.COM
    </li>
    <li>
      <svg viewBox="0 0 24 24" fill="none" stroke="var(--accent)" stroke-width="2"><rect x="3" y="6" width="18" height="13" rx="1"/><path d="M3 7l9 7 9-7"/></svg>
      OFFICE@TRV-GROUNDMAKRZ.COM
    </li>
  </ul>
</section>

</body>
</html>
```